Crispy Jerky Packaging for KO.LU

We need packaging for for our hand-crafted crispy beef jerky. We are launching a new product that is like eating a potato chip, but made of beef/pork. We would like to have a window for people to be able to see our product. It is a new type of jerky, so we need the audience to be able to see that they are getting value for what they are paying for. Where a traditional 1oz portion of jerky would have 10-11g protein, ours has 20g of protein. It is also easy on the jaw because there is no tearing off of the jerky, it eats just like a chip

Target Market(s)

Beer lovers/ health-conscious/ millenials

Industry/Entity Type

Product

Font styles to use
Other font styles liked:
• be creative

Colors
fbed22
9bcb3b
85cae6

Requirements
Must have
• Yellow packaging base
• 20g Protein per serving
• Made in Hawaii
Nice to have
• Would prefer the current font we have for the company name, KO.LU
Should not have
• cows

```html
<!DOCTYPE html>
<html lang="en">
<head>
<meta charset="utf-8">
<title>KO.LU Crispy Beef Jerky – Pouch Front</title>
<link rel="stylesheet" href="https://fonts.googleapis.com/css2?family=Open+Sans:wght@700;800&family=Kaushan+Script&display=swap">
<style>
  :root {
    --page-bg: #ececec;
    --pouch-yellow: #f5c11a;
    --pouch-yellow-deep: #e9ad12;
    --ink-black: #0d0d0d;
    --paper-white: #ffffff;
    --jerky-dark: #4a1a1c;
    --jerky-mid: #7a2a28;
    --jerky-warm: #a0473a;
  }
  * { margin: 0; padding: 0; box-sizing: border-box; }
  html, body {
    width: 1200px;
    height: 1182px;
    overflow: hidden;
    background: var(--page-bg);
  }
  .canvas {
    position: relative;
    width: 1200px;
    height: 1182px;
  }
  .pouch {
    position: absolute;
    left: 344px;
    top: 92px;
    width: 508px;
    height: 888px;
    border-radius: 18px;
    overflow: hidden;
    background: linear-gradient(180deg, var(--pouch-yellow) 0%, var(--pouch-yellow) 70%, var(--pouch-yellow-deep) 100%);
  }
  .pouch__top-band {
    position: absolute;
    left: 0;
    top: 0;
    width: 508px;
    height: 340px;
  }
  .brand-name {
    position: absolute;
    left: 52px;
    top: 150px;
    font-family: "Open Sans", sans-serif;
    font-weight: 800;
    font-size: 100px;
    line-height: 1;
    letter-spacing: 1px;
    color: var(--paper-white);
    transform: rotate(-11deg);
    transform-origin: left bottom;
  }
  .product-title {
    position: absolute;
    font-family: "Kaushan Script", cursive;
    font-size: 66px;
    color: var(--ink-black);
    line-height: 1;
    white-space: nowrap;
    transform: rotate(-9deg);
    transform-origin: left bottom;
  }
  .product-title--crispy { left: 36px;  top: 318px; }
  .product-title--beef   { left: 232px; top: 340px; }
  .product-title--jerky  { left: 300px; top: 392px; }
  .product-window {
    position: absolute;
    left: 200px;
    top: 480px;
    width: 262px;
    height: 386px;
    border-radius: 36px 70px 48px 26px;
    background:
      radial-gradient(ellipse at 40% 60%, var(--jerky-warm) 0%, transparent 55%),
      linear-gradient(160deg, var(--jerky-mid) 0%, var(--jerky-dark) 100%);
  }
  .claims {
    position: absolute;
    left: 48px;
    top: 810px;
    padding-left: 5px;
    border-left: 2px solid var(--ink-black);
    font-family: "Open Sans", sans-serif;
    font-weight: 700;
    color: var(--ink-black);
  }
  .claims__protein-amount { font-size: 22px; line-height: 1.05; }
  .claims__line { font-size: 10.5px; line-height: 1.3; white-space: nowrap; }
</style>
</head>
<body>
<main class="canvas">
  <section class="pouch" aria-label="KO.LU crispy beef jerky pouch front">
    <svg class="pouch__top-band" viewBox="0 0 508 340" aria-hidden="true">
      <polygon points="0,0 508,0 508,204 0,320" fill="var(--ink-black)"/>
      <polygon points="0,320 508,204 508,210 0,328" fill="var(--paper-white)"/>
    </svg>

    <div class="brand-name">KO.LU</div>

    <div class="product-title product-title--crispy">Crispy</div>
    <div class="product-title product-title--beef">Beef</div>
    <div class="product-title product-title--jerky">Jerky</div>

    <div class="product-window" role="img" aria-label="Clear window showing pieces of crispy beef jerky inside the pouch"></div>

    <div class="claims">
      <div class="claims__protein-amount">20g</div>
      <div class="claims__line">Protein per serving</div>
      <div class="claims__line">Made in Hawaii</div>
    </div>
  </section>
</main>
</body>
</html>
```